Interior Design/ decoration business card design

This card is for my Interior Design and Decoration business and later I will also be selling homewares. I would like the card to be very simple in design and like either white, duck egg blue , aquas or metallics on a flat mat card excellent quality card. It needs to be well designed as that is my field. I dont like fuss, the simpler the better. I would like a styalised brim under the name brim if possible. SIMPLE, STYLISH, CLASSIC, TASTEFUL

Target Market(s)

40 + year olds who are building or rennovating.

Industry/Entity Type

Business

Contact Information for Business Card

Brim
styling, design, homeware

Marnie Callow
p 0427163958
e marnie@brimhouse.com.au
w brimhouse.com.au

Requirements
Must have
• very simple, stylish, classic, sophisticated. Simple and easy to read text that is a print similar to attached image. I like simple round A's though not as in attached image.

Double sided. It wont save as double sided for some reason!!
Should not have
• not too much colour, No animated / cartoon pictures.

```html
<!DOCTYPE html>
<html lang="en">
<head>
<meta charset="utf-8">
<title>Brim – Business Card</title>
<link rel="stylesheet" href="https://fonts.googleapis.com/css2?family=Exo+2:wght@300;400;600&display=swap">
<style>
  :root {
    --backdrop: #d9d7d4;
    --paper: #ffffff;
    --umber: #4b4038;
    --charcoal: #343434;
    --ink: #3a3430;
    --on-dark: #f4f1ec;
    --shadow: rgba(0,0,0,0.18);
  }
  * { margin: 0; padding: 0; box-sizing: border-box; }
  html, body { width: 1200px; height: 892px; overflow: hidden; }
  body {
    background: var(--backdrop);
    font-family: "Exo 2", sans-serif;
    position: relative;
  }
  .card {
    position: absolute;
    top: 148px;
    width: 340px;
    height: 596px;
    background: var(--paper);
    box-shadow: 0 10px 28px var(--shadow);
    overflow: hidden;
  }
  .card--back { left: 210px; }
  .card--front { left: 650px; }

  .wordmark {
    position: absolute;
    left: 0; right: 0;
    text-align: center;
    font-weight: 300;
    color: var(--ink);
    letter-spacing: 2px;
    line-height: 1;
  }
  .card--back .wordmark { top: 230px; font-size: 58px; }
  .card--front .wordmark { top: 104px; font-size: 62px; }

  .back-band {
    position: absolute;
    left: 0; right: 0; bottom: 0;
    height: 64px;
    background: var(--umber);
    display: flex;
    align-items: center;
    justify-content: center;
    color: var(--on-dark);
    font-size: 15px;
    letter-spacing: 1.5px;
  }

  .contact-stack {
    position: absolute;
    left: 22px; right: 22px; top: 262px;
    display: flex;
    flex-direction: column;
    gap: 10px;
  }
  .contact-bar {
    border-radius: 9px;
    background: var(--umber);
    color: var(--on-dark);
    display: flex;
    align-items: center;
    height: 64px;
    padding-right: 14px;
  }
  .contact-bar--name {
    background: var(--charcoal);
    height: 96px;
    padding-left: 24px;
    flex-direction: column;
    align-items: flex-start;
    justify-content: center;
  }
  .person-name {
    font-size: 25px;
    font-weight: 600;
    letter-spacing: 2px;
    text-transform: uppercase;
    white-space: nowrap;
  }
  .person-role {
    font-size: 12px;
    letter-spacing: 2.5px;
    text-transform: uppercase;
    margin-top: 5px;
  }
  .bar-icon {
    width: 54px;
    flex: 0 0 54px;
    display: flex;
    justify-content: center;
  }
  .bar-icon svg { width: 21px; height: 21px; fill: var(--on-dark); }
  .bar-text {
    font-size: 15px;
    letter-spacing: 1px;
    line-height: 1.45;
    white-space: nowrap;
  }
</style>
</head>
<body>

  <section class="card card--back" aria-label="Card back">
    <div class="wordmark">brim</div>
    <div class="back-band">www.brimhouse.com.au</div>
  </section>

  <section class="card card--front" aria-label="Card front">
    <div class="wordmark">brim</div>

    <div class="contact-stack">
      <div class="contact-bar contact-bar--name">
        <div class="person-name">Marnie Callow</div>
        <div class="person-role">General Manager</div>
      </div>

      <div class="contact-bar">
        <div class="bar-icon">
          <svg viewBox="0 0 24 24" aria-hidden="true"><path d="M12 3 2 11.5h3V21h5.5v-6h3v6H19v-9.5h3z"/></svg>
        </div>
        <div class="bar-text">42 Fenwick Lane,<br>Level 3 Harbour Street W.</div>
      </div>

      <div class="contact-bar">
        <div class="bar-icon">
          <svg viewBox="0 0 24 24" aria-hidden="true"><path d="M6.6 10.8a15.1 15.1 0 0 0 6.6 6.6l2.2-2.2a1 1 0 0 1 1-.25 11.4 11.4 0 0 0 3.6.57 1 1 0 0 1 1 1V20a1 1 0 0 1-1 1A17 17 0 0 1 3 4a1 1 0 0 1 1-1h3.5a1 1 0 0 1 1 1c0 1.25.2 2.45.57 3.6a1 1 0 0 1-.25 1z"/></svg>
        </div>
        <div class="bar-text">0427 163 958</div>
      </div>

      <div class="contact-bar">
        <div class="bar-icon">
          <svg viewBox="0 0 24 24" aria-hidden="true"><path d="M3 4h18v12H3zm2 2v8h14V6zM9 18h6v2H9z"/></svg>
        </div>
        <div class="bar-text">marnie@brimhouse.com.au<br>www.brimhouse.com.au</div>
      </div>
    </div>
  </section>

</body>
</html>
```